Car rental website design for a UAE car rental company

This project is about creating a new website design for a car rental company located in Dubai (United Arab Emirates), I opened the same project a few months ago but I didn't receive a lot of appealing entries so I closed it but this time I am marking the project as guaranteed to avoid such situation again, if you have already provided a design before then please re-submit again on this project so that it is considered while reviewing all the designs

A few important things:

1- We need a simple non-complex design
2- The final deliverable would be 2 screens (PSD, JPEG ... etc), the first screen is for the home page and the second screen is for an internal page
3- The home page must have a section that end users can use to rent a car online directly from the home page instead of going into some inner pages
4- The current website is very old and not very appealing so avoid creating a similar design (www.crestvane-autos.example)
5- The name is Crestvane but the company rents normal cars (no Limousin cars will be rented) so avoid adding any fancy cars in the images/graphics used in the design, just normal end users cars
6- The expected pages would be: home, About us, Our team, Strategy, Contact us and links to social media pages
7- The attachments include the company's logo and some screens from other car rental companies that provide online rentals/payments

If you have any questions please feel free to ask and please note that we will need the designs urgently

Thanks

Target Market(s)

Dubai - United Arab Emirates

Industry/Entity Type

It Company

Number of Pages Required

2 page

Font styles to use
Sans Serif

Requirements
Must have
• Check the project details
Nice to have
Should not have

```html
<!DOCTYPE html>
<html lang="en">
<head>
<meta charset="utf-8">
<title>Crestvane Rent A Car</title>
<link href="https://fonts.googleapis.com/css2?family=Roboto+Slab:wght@300;400&family=Roboto+Condensed:wght@300;400&family=Open+Sans:wght@400;600&display=swap" rel="stylesheet">
<style>
:root{
  --maroon:#a4103f;
  --grey-text:#8b9090;
  --ink:#2f2f2f;
  --soft-bg:#f4f4f4;
  --header-bg:#eef3f8;
  --tab-grey:#8f9a95;
  --placeholder:#e6e8ea;
  --white:#ffffff;
}
*{margin:0;padding:0;box-sizing:border-box}
html,body{width:920px;height:1200px;overflow:hidden;background:var(--white)}
body{position:relative;font-family:"Roboto Slab",serif;color:var(--ink)}
.abs{position:absolute;white-space:nowrap}

/* header */
.site-header{position:absolute;left:0;top:0;width:920px;height:80px;background:var(--header-bg);border-bottom:2px solid var(--maroon)}
.brand{position:absolute;left:61px;top:22px;display:flex;align-items:center;gap:10px}
.brand-square{width:34px;height:34px;background:var(--maroon)}
.brand-name{font-family:"Roboto Slab",serif;font-weight:400;font-size:27px;color:var(--maroon);letter-spacing:.5px}
.social{display:flex;gap:7px}
.social span{display:block;width:17px;height:17px;border-radius:50%;background:var(--grey-text)}
.header-social{position:absolute;left:463px;top:15px}
.call{position:absolute;left:647px;top:9px;display:flex;align-items:center;gap:8px;font-family:"Roboto Condensed",sans-serif;font-size:16px;color:var(--maroon)}
.main-nav{position:absolute;left:463px;top:54px;display:flex;gap:19px;font-family:"Roboto Slab",serif;font-weight:300;font-size:12.5px;color:var(--grey-text)}
.main-nav .current{color:var(--maroon)}

/* hero */
.hero{position:absolute;left:0;top:80px;width:920px;height:338px;border-bottom:3px solid var(--maroon);
  background:linear-gradient(180deg,#9fb0c3 0%,#c3ccd6 45%,#8c96a0 75%,#5a6068 100%)}
.hero-headline{position:absolute;left:67px;top:18px;width:380px;font-family:"Roboto Condensed",sans-serif;font-weight:300;font-size:24px;line-height:29px;color:var(--white)}

/* booking */
.booking{position:absolute;left:538px;top:80px;width:321px;height:336px;background:var(--maroon)}
.tab-active{position:absolute;left:4px;top:5px;width:82px;height:29px;background:var(--tab-grey);color:var(--white);font-size:13px;line-height:31px;text-align:center}
.tab-link{position:absolute;left:94px;top:11px;color:var(--white);font-size:11.5px;white-space:nowrap}
.booking-body{position:absolute;left:4px;top:34px;width:314px;height:298px;background:var(--white);font-size:11px;color:var(--ink)}
.step{position:absolute;width:19px;height:19px;border:1px solid var(--maroon);font-size:11px;line-height:17px;text-align:center}
.link{color:var(--maroon);text-decoration:underline}
.field{position:absolute;height:21px;border:1px solid #a9a9a9;font-size:9.5px;line-height:19px;padding-left:6px;color:var(--ink)}
.spin{position:absolute;right:0;top:0;width:16px;height:19px;border-left:1px solid #a9a9a9;font-size:6px;line-height:9px;text-align:center;color:#666}
.check{display:inline-block;width:7px;height:7px;border:1px solid #555;margin-right:4px;vertical-align:1px}
.help{position:absolute;width:16px;height:16px;border-radius:50%;background:#a7aaa7;color:var(--white);font-size:9px;line-height:16px;text-align:center}
.quote-btn{position:absolute;left:203px;top:268px;width:102px;height:30px;background:var(--maroon);color:var(--white);font-size:13px;line-height:30px;text-align:center}

/* features */
.features{position:absolute;left:0;top:418px;width:920px;height:208px;background:var(--soft-bg)}
.feature{position:absolute;top:26px;width:200px;text-align:center}
.feature-icon{width:72px;height:72px;margin:0 auto;border-radius:50%;border:2px solid #9a9d9d;display:flex;align-items:center;justify-content:center}
.feature-icon.active{border-color:var(--maroon)}
.feature-title{margin-top:13px;font-size:12px;line-height:16px;color:var(--ink)}
.feature-text{width:164px;margin:4px auto 0;font-family:"Open Sans",sans-serif;font-size:11px;line-height:15.5px;color:#555}
.slider-arrow{position:absolute;top:92px}

/* headings */
.section-title{position:absolute;left:0;width:920px;text-align:center;font-weight:300;font-size:14.5px;color:var(--grey-text)}
.section-title em{font-style:normal;color:var(--maroon);font-weight:400}
.dashed{position:absolute;border-top:1px dashed #9aa0a0;height:0}
.divider{position:absolute;left:64px;width:792px;height:8px;background:radial-gradient(ellipse at top,rgba(0,0,0,.08),rgba(0,0,0,0) 70%)}

/* deals */
.deal{position:absolute;top:696px;width:168px;text-align:center}
.deal-photo{width:168px;height:88px;background:var(--placeholder)}
.deal-price{margin-top:19px;font-family:"Roboto Condensed",sans-serif;font-size:13px;color:var(--ink)}
.deal-price.featured{color:var(--maroon)}

/* text blocks */
.prose{position:absolute;left:0;width:920px;text-align:center;font-weight:300;font-size:10.5px;line-height:17px;color:var(--ink);white-space:nowrap}
.read-more{position:absolute;left:0;top:966px;width:920px;text-align:center;font-size:11.5px}

/* footer */
.site-footer{position:absolute;left:0;top:1155px;width:920px;height:45px;background:var(--maroon)}
.footer-nav{position:absolute;left:62px;top:15px;display:flex;gap:14px;font-size:11px;font-weight:300;color:var(--white)}
.footer-social{position:absolute;left:511px;top:13px}
.footer-social span{background:#d9a9b8;border:1px solid var(--white)}
.copyright{position:absolute;right:59px;top:15px;font-family:"Open Sans",sans-serif;font-weight:600;font-size:10.5px;color:var(--white)}
</style>
</head>
<body>

<header class="site-header">
  <div class="brand"><span class="brand-square"></span><span class="brand-name">Crestvane</span></div>
  <div class="social header-social"><span></span><span></span><span></span><span></span></div>
  <div class="call">
    <svg width="22" height="26" viewBox="0 0 22 26" aria-hidden="true"><path d="M4 14V10a7 7 0 0 1 14 0v4" fill="none" stroke="#8b9090" stroke-width="2.5"/><rect x="1" y="12" width="5" height="8" rx="2" fill="#a4103f"/><rect x="16" y="12" width="5" height="8" rx="2" fill="#a4103f"/><path d="M18 20q0 4-6 4" fill="none" stroke="#8b9090" stroke-width="1.5"/></svg>
    <span>Call us at +971 4 555 0182</span>
  </div>
  <nav class="main-nav"><span class="current">HOME</span><span>ABOUT US</span><span>OUR TEAM</span><span>STRATEGY</span><span>CONTACT US</span></nav>
</header>

<section class="hero" role="img" aria-label="Silver family sedan parked in front of a lake and mountain landscape">
  <h1 class="hero-headline">Experience An Extra Mile of comfort, pleasure and leisure From the best</h1>
</section>

<section class="booking">
  <div class="tab-active">Book A Car</div>
  <div class="tab-link">View / Modify / Cancel A Reservation</div>
  <div class="booking-body">
    <div class="step" style="left:3px;top:9px">1</div>
    <div class="abs" style="left:36px;top:10px">Pick-up Location &nbsp;(City, State or Airport Code</div>
    <div class="abs link" style="left:36px;top:28px">Previous Searches</div>
    <div class="field" style="left:36px;top:48px;width:260px">Dubai Airport - Terminal 3</div>
    <div class="abs link" style="left:36px;top:73px">Help me find a rental location</div>
    <div class="abs" style="left:36px;top:94px"><span class="check"></span>Return car to a different Crestvane Location</div>
    <div class="help" style="left:266px;top:93px">?</div>

    <div class="step" style="left:3px;top:120px">2</div>
    <div class="abs" style="left:36px;top:121px">Pick-up Date &amp; Time</div>
    <div class="field" style="left:36px;top:140px;width:128px">26/03/2015</div>
    <div class="field" style="left:168px;top:140px;width:128px">16:00<span class="spin">^<br>v</span></div>
    <div class="abs" style="left:36px;top:170px">Return Date &amp; Time</div>
    <div class="field" style="left:36px;top:188px;width:128px">26/03/2015</div>
    <div class="field" style="left:168px;top:188px;width:128px">16:00<span class="spin">^<br>v</span></div>
    <div class="abs" style="left:36px;top:219px">Hire Car Type</div>
    <div class="field" style="left:36px;top:237px;width:128px">Automatic</div>
    <div class="abs" style="left:170px;top:241px;font-size:10px"><span class="check"></span>Apply a discount Code</div>
    <div class="help" style="left:297px;top:239px">?</div>
    <div class="quote-btn">Get A Quote</div>
  </div>
</section>

<section class="features">
  <svg class="slider-arrow" style="left:32px" width="10" height="18" viewBox="0 0 10 18" aria-hidden="true"><path d="M9 1 1 9l8 8" fill="none" stroke="#dcdcdc" stroke-width="1.5"/></svg>
  <svg class="slider-arrow" style="left:877px" width="10" height="18" viewBox="0 0 10 18" aria-hidden="true"><path d="M1 1l8 8-8 8" fill="none" stroke="#dcdcdc" stroke-width="1.5"/></svg>

  <div class="feature" style="left:54px">
    <div class="feature-icon active">
      <svg width="48" height="36" viewBox="0 0 48 36" aria-hidden="true"><g fill="#a4103f"><path d="M4 14l4-9h14l4 9h2v8H2v-8z"/><circle cx="8" cy="23" r="3"/><circle cx="22" cy="23" r="3"/><path d="M20 24l4-8h14l4 8h2v8H18v-8z" stroke="#fff" stroke-width="1.5"/><circle cx="24" cy="33" r="3"/><circle cx="38" cy="33" r="3"/></g></svg>
    </div>
    <div class="feature-title">Wide Range Of Vehicles For City<br>Driving or SUV’s For Trips</div>
    <div class="feature-text">Lorem ipsum dolor sit<br>aonsectetuer adipiscing elied<br>diam nonummy</div>
  </div>
  <div class="feature" style="left:270px">
    <div class="feature-icon">
      <svg width="36" height="36" viewBox="0 0 36 36" aria-hidden="true"><path d="M4 16 16 4h12v12L16 28z" fill="#8b9090" transform="rotate(10 18 18)"/><circle cx="23" cy="10" r="2.5" fill="#fff"/><text x="13" y="22" font-size="8" fill="#fff" font-family="Open Sans,sans-serif">%</text></svg>
    </div>
    <div class="feature-title">Special 10% Discount For New<br>Customers On The First Rent</div>
    <div class="feature-text">Lorem ipsum dolor sit<br>aonsectetuer adipiscing elied<br>diam nonummy</div>
  </div>
  <div class="feature" style="left:475px">
    <div class="feature-icon">
      <svg width="40" height="40" viewBox="0 0 40 40" aria-hidden="true"><g fill="#8b9090"><circle cx="14" cy="8" r="5"/><rect x="17" y="6" width="14" height="4"/><path d="M6 26l4-9h20l4 9h1v8H5v-8z"/><rect x="7" y="33" width="5" height="5"/><rect x="28" y="33" width="5" height="5"/></g><circle cx="11" cy="29" r="2" fill="#fff"/><circle cx="29" cy="29" r="2" fill="#fff"/></svg>
    </div>
    <div class="feature-title">Long Term Car<br>Rentals</div>
    <div class="feature-text">Lorem ipsum dolor sit<br>aonsectetuer adipiscing elied<br>diam nonummy</div>
  </div>
  <div class="feature" style="left:680px">
    <div class="feature-icon">
      <svg width="36" height="36" viewBox="0 0 36 36" aria-hidden="true"><path d="M14 10h8a9 9 0 0 1 0 18h-2" fill="none" stroke="#8b9090" stroke-width="5"/><path d="M4 10l11-8v16z" fill="#8b9090"/></svg>
    </div>
    <div class="feature-title">Buyback Option After<br>Lease Term</div>
    <div class="feature-text">Lorem ipsum dolor sit<br>aonsectetuer adipiscing elied<br>diam nonummy</div>
  </div>
</section>

<h2 class="section-title" style="top:650px">Grab the <em>Best Deal Today</em></h2>
<div class="dashed" style="left:328px;top:674px;width:264px"></div>

<div class="deal" style="left:74px"><div class="deal-photo" role="img" aria-label="Photo of a silver rental sedan"></div><div class="deal-price featured">From Only AED 1100 p/m</div></div>
<div class="deal" style="left:276px"><div class="deal-photo" role="img" aria-label="Photo of a red rental sedan"></div><div class="deal-price">From Only AED 1100 p/m</div></div>
<div class="deal" style="left:478px"><div class="deal-photo" role="img" aria-label="Photo of a silver rental sedan"></div><div class="deal-price">From Only AED 1100 p/m</div></div>
<div class="deal" style="left:680px"><div class="deal-photo" role="img" aria-label="Photo of a red rental sedan"></div><div class="deal-price">From Only AED 1100 p/m</div></div>

<div class="divider" style="top:834px"></div>

<h2 class="section-title" style="top:865px">Welcome to Crestvane <em>Rent A Car</em></h2>
<div class="dashed" style="left:280px;top:888px;width:360px"></div>
<p class="prose" style="top:893px">As Dubai is expected to welcome millions of tourists and visitors, car rental industry is believed to escalate more rapidly in the region.<br>Over the past five years, demands for car rentals in Dubai has been augmenting at a healthy pace and is currently registering a growth<br>rate of 20 to 25 percent per year. The swift economic growth and the number. Crestvane was established to bring comfort<br>and pleasure to all its clients. First rate service plus highly maintained and top...</p>
<div class="read-more">Read More</div>

<div class="divider" style="top:1004px"></div>

<h2 class="section-title" style="top:1035px">Our <em>Mission</em></h2>
<div class="dashed" style="left:352px;top:1058px;width:216px"></div>
<p class="prose" style="top:1071px">To be one of the leading auto leasing company in the fast growing economy and tourism industry of the emirate of Dubai &amp; play alongside<br>with the major car rental companies in the globe.<br><span style="display:block;margin-top:3px">Crestvane vows to deliver comfort, luxury &amp; satisfaction to all our clients by providing them professional, hassle-free and first class service.</span></p>

<footer class="site-footer">
  <nav class="footer-nav"><span>HOME</span><span>ABOUT US</span><span>OUR TEAM</span><span>STRATEGY</span><span>CONTACT US</span></nav>
  <div class="social footer-social"><span></span><span></span><span></span><span></span></div>
  <div class="copyright">© 2015 Crestvane. All Rights Reserved</div>
</footer>

</body>
</html>
```